Cedar Brook Stables, LLC

Equestrian business card to promote equine retirement, farm sitting, short term board. Located in Aiken, SC.
Updates
Updated color schemes.
Contact Information for Business Card
Contact info, description of work.
Colors
0094D4
00A9DD
6FCCEA
C7EBF8
E9F6FB
59FF00
82FF00
B8FF75
E3FFCB
F4FFEA
F0912C
F2A743
F7CA91
FBE8D2
FDF5EE

```html
<!DOCTYPE html>
<html lang="en">
<head>
<meta charset="utf-8">
<title>Cedar Brook Stables – Business Card</title>
<link rel="stylesheet" href="https://fonts.googleapis.com/css2?family=Poppins:wght@400;500;600;700&display=swap">
<style>
  :root {
    --backdrop: #1c1816;
    --card: #262626;
    --green: #087a0a;
    --orange: #f7940f;
    --gold: #f2b400;
    --white: #ffffff;
  }
  * { margin: 0; padding: 0; box-sizing: border-box; }
  html, body { width: 1200px; height: 842px; overflow: hidden; }
  body {
    background: var(--backdrop);
    font-family: "Poppins", sans-serif;
    position: relative;
  }
  .card {
    position: absolute;
    width: 540px;
    height: 309px;
    background: var(--card);
    overflow: hidden;
    box-shadow: 0 18px 40px rgba(0,0,0,.55);
  }
  /* Contact side */
  .card--contact { left: 36px; top: 266px; }
  .card--contact .band {
    position: absolute; left: 0; right: 0; height: 13px; background: var(--green);
  }
  .band--top { top: 0; }
  .band--bottom { bottom: 0; }
  .contact {
    position: absolute; inset: 0;
    display: flex; flex-direction: column; align-items: center; justify-content: center;
    text-align: center; color: var(--gold); text-transform: uppercase;
  }
  .contact__name { font-weight: 700; font-size: 21px; letter-spacing: .5px; line-height: 1.1; }
  .contact__role { font-size: 13px; letter-spacing: .5px; }
  .contact__rule { width: 62px; height: 1px; background: #3f9a1a; margin: 9px 0; }
  .contact__line { font-size: 13.5px; line-height: 1.3; letter-spacing: .3px; }
  .contact__line--phone { font-size: 16px; }

  /* Brand side */
  .card--brand { left: 624px; top: 266px; }
  .tab { position: absolute; }
  .tab--left { left: 0; top: 120px; width: 46px; height: 70px; background: var(--orange); }
  .tab--left-line { left: 52px; top: 118px; width: 5px; height: 74px; background: var(--green); }
  .tab--right { right: 0; top: 62px; width: 44px; height: 70px; background: var(--orange); }
  .tab--right-line { right: 50px; top: 60px; width: 5px; height: 74px; background: var(--green); }
  .brand {
    position: absolute; left: 0; right: 0; top: 78px;
    display: flex; flex-direction: column; align-items: center;
  }
  .brand__dot { width: 62px; height: 62px; border-radius: 50%; background: var(--gold); margin-bottom: 12px; }
  .brand__name { color: var(--white); font-weight: 600; font-size: 19px; letter-spacing: .3px; }
  .services {
    position: absolute; left: 0; right: 0; bottom: 62px;
    text-align: center; color: var(--orange); font-size: 13px; font-weight: 500;
  }
</style>
</head>
<body>
  <section class="card card--contact" aria-label="Contact side">
    <div class="band band--top"></div>
    <div class="contact">
      <p class="contact__name">Daniel Hartley</p>
      <p class="contact__role">Managing Director</p>
      <div class="contact__rule"></div>
      <p class="contact__line contact__line--phone">803-555 014 227</p>
      <p class="contact__line">hello@cedarbrookmail.com</p>
      <p class="contact__line">www.cedarbrookstables.com</p>
      <div class="contact__rule"></div>
      <p class="contact__line">118, Whiskey Road Lane</p>
      <p class="contact__line">29801, Aiken SC</p>
    </div>
    <div class="band band--bottom"></div>
  </section>

  <section class="card card--brand" aria-label="Brand side">
    <div class="tab tab--left"></div>
    <div class="tab tab--left-line"></div>
    <div class="tab tab--right"></div>
    <div class="tab tab--right-line"></div>
    <div class="brand">
      <div class="brand__dot"></div>
      <p class="brand__name">Cedar Brook Stables, LLC</p>
    </div>
    <p class="services">Short Term Board | Farm Sitting | Equine Retirement</p>
  </section>
</body>
</html>
```